Detail Shop Business card design

i need a business card design for my new detailing company called 'Brisk's Polish Works'. i want an all black and white design . simple, direct and to the point. i want the designer to choose a fitting font to match the logothe front should have logo, address, phone and email and the back side should have a slogan and text indicating that we offer services on anything including cars, trucks, motorcycles and RVs. slogan will read "we take pride in your ride"
maybe also very small on the back side the IG icon with Brisks_Polish_Works

phone 208.417.6352
address 3847 E Larkin Ave
Spokane WA 99214
email: BrisksPolish@mailvexo.com

Target Market(s)

all ages , auto enthusiasts

Industry/Entity Type

Automotive

Contact Information for Business Card

the front should have logo, address, phone and email and the back side should have a slogan and text indicating that we offer services on anything including cars, trucks, motorcycles and RVs. slogan will read "we take pride in your ride"

phone 208.417.6352
address 3847 E Larkin Ave
Spokane WA 99214

Colors
000000
ffffff

Requirements
Must have
• bold font and very simple design with good spacing
Nice to have
• anything creative from the designer indicating we service any types of vehicles
Should not have
• any colors ,

```html
<!DOCTYPE html>
<html lang="en">
<head>
<meta charset="utf-8">
<title>Brisk's Polish Works – Business Card</title>
<link rel="stylesheet" href="https://fonts.googleapis.com/css2?family=Alfa+Slab+One&family=Noto+Serif:ital,wght@0,400;0,700;1,400&display=swap">
<style>
  :root {
    --ink: #000000;
    --paper: #ffffff;
    --table: #2b2b2b;
    --card-w: 600px;
    --card-h: 343px;
  }
  * { margin: 0; padding: 0; box-sizing: border-box; }
  html, body { width: 1200px; height: 900px; overflow: hidden; }
  body {
    background: var(--table);
    font-family: "Noto Serif", Georgia, serif;
    display: flex;
    flex-direction: column;
    align-items: center;
    justify-content: center;
    gap: 60px;
  }
  .card {
    position: relative;
    width: var(--card-w);
    height: var(--card-h);
    border-radius: 22px;
    overflow: hidden;
    background: var(--ink);
    color: var(--paper);
  }

  /* Back side */
  .back { padding: 34px 44px; }
  .slogan {
    font-family: "Alfa Slab One", "Rockwell", serif;
    font-size: 46px;
    font-weight: 400;
    line-height: 1.05;
    text-transform: uppercase;
    letter-spacing: 1px;
    text-align: center;
  }
  .rule { height: 2px; background: var(--paper); }
  .back .rule.top { margin-top: 22px; }
  .services {
    display: flex;
    justify-content: space-between;
    list-style: none;
    font-size: 17px;
    margin: 14px 6px 26px;
  }
  .services li::before { content: "\2022"; margin-right: 6px; }
  .handle-row {
    display: flex;
    align-items: center;
    gap: 14px;
    font-style: italic;
    font-size: 16px;
  }
  .handle-row .rule { flex: 1; }
  .handle-mark {
    width: 14px; height: 14px;
    border: 2px solid var(--paper);
    border-radius: 3px;
  }
  .back .rule.bottom { margin: 26px 60px 0; }

  /* Front side */
  .front .split { position: absolute; inset: 0; }
  .brand {
    position: absolute;
    left: 16px; top: 0;
    width: 164px; height: 100%;
    display: flex;
    flex-direction: column;
    align-items: center;
    justify-content: center;
    gap: 12px;
    color: var(--ink);
    text-align: center;
  }
  .brand-dot { width: 24px; height: 24px; border-radius: 50%; background: var(--ink); }
  .brand-name {
    font-weight: 700;
    font-size: 21px;
    line-height: 1.2;
    white-space: nowrap;
  }
  .contact {
    position: absolute;
    left: 270px; right: 20px; top: 0; height: 100%;
    display: flex;
    flex-direction: column;
    align-items: center;
    justify-content: center;
    text-align: center;
  }
  .person { font-weight: 700; font-size: 26px; }
  .role { font-size: 15px; margin-top: 2px; }
  .contact .rule { width: 80px; height: 2px; margin: 16px 0; }
  .line { font-size: 17px; line-height: 1.4; }
</style>
</head>
<body>

  <section class="card back" aria-label="Card back">
    <h1 class="slogan">We take pride<br>in your ride</h1>
    <div class="rule top"></div>
    <ul class="services">
      <li>Auto</li>
      <li>Motorcycle</li>
      <li>Boat</li>
      <li>RV</li>
    </ul>
    <div class="handle-row">
      <div class="rule"></div>
      <span class="handle-mark"></span>
      <span class="handle">Brisks_Polish_Works</span>
      <div class="rule"></div>
    </div>
    <div class="rule bottom"></div>
  </section>

  <section class="card front" aria-label="Card front">
    <svg class="split" width="600" height="343" viewBox="0 0 600 343">
      <rect width="600" height="343" fill="var(--paper)"/>
      <polygon points="232,0 250,0 210,171 250,343 232,343 192,171" fill="var(--ink)"/>
      <polygon points="262,0 600,0 600,343 262,343 222,171" fill="var(--ink)"/>
    </svg>
    <div class="brand">
      <span class="brand-dot"></span>
      <p class="brand-name">Brisk's<br>Polish Works</p>
    </div>
    <div class="contact">
      <p class="person">Dane Corwell</p>
      <p class="role">Owner</p>
      <div class="rule"></div>
      <p class="line">208.417.6352</p>
      <p class="line">BrisksPolish@mailvexo.com</p>
      <div class="rule"></div>
      <p class="line">3847 E Larkin Ave</p>
      <p class="line">Spokane WA 99214</p>
    </div>
  </section>

</body>
</html>
```